Quorva - corporate Business Card

We need a good look and innovative business card for a new start up company based in Los Angeles called "Quorva". We are in a payment business, including payment card, app, and ewallet. We are expert in online payment and Card not present (CNP) transaction.
We need an innovative, modern business card.

Our logo font is Aero Matics

Target Market(s)

Startup - Bank - Online Payment - Card Manufacturing

Industry/Entity Type

Startup

Contact Information for Business Card

phone: 555 014 7396 - Address: 4172 Marlowe blvd, Ashfield Park, NV 89431

Requirements
Must have
• Message: innovative, professional, expert, high tech, trust, online payment expert, security
Nice to have
• no comment
Should not have
• no Comment

```html
<!DOCTYPE html>
<html lang="en">
<head>
<meta charset="utf-8">
<title>Quorva – Business Card</title>
<link rel="stylesheet" href="https://fonts.googleapis.com/css2?family=Exo+2:wght@500&family=Lato:wght@400;700&display=swap">
<style>
  :root {
    --brand-red: #b51e2d;
    --paper: #fafafa;
    --backdrop: #ececec;
    --ink: #1e1e1e;
    --white: #ffffff;
    --faint-white: rgba(255,255,255,0.14);
  }
  * { margin: 0; padding: 0; box-sizing: border-box; }
  html, body { width: 1200px; height: 586px; overflow: hidden; }
  body { background: var(--backdrop); font-family: "Lato", sans-serif; position: relative; }

  .card { position: absolute; top: 129px; width: 502px; height: 301px; overflow: hidden; }

  /* Back side */
  .card--back { left: 61px; background: var(--brand-red); }
  .card--back .halo {
    position: absolute; left: 120px; top: 19px; width: 260px; height: 260px;
    border-radius: 50%; background: var(--faint-white);
  }
  .card--back .wordmark {
    position: absolute; left: 0; right: 0; top: 124px; text-align: center;
    font-family: "Exo 2", sans-serif; font-weight: 500; font-size: 44px;
    color: var(--white); line-height: 1;
  }
  .card--back .website {
    position: absolute; left: 0; right: 0; top: 267px; text-align: center;
    font-family: "Lato", sans-serif; font-weight: 700; font-size: 12px;
    letter-spacing: 3.2px; color: var(--white);
  }

  /* Front side */
  .card--front { left: 619px; background: var(--paper); }
  .brand { position: absolute; left: 145px; top: 33px; display: flex; align-items: center; gap: 9px; }
  .brand .dot { width: 64px; height: 64px; border-radius: 50%; background: var(--brand-red); }
  .brand .wordmark {
    font-family: "Exo 2", sans-serif; font-weight: 500; font-size: 45px;
    color: var(--brand-red); line-height: 1; margin-top: -4px;
  }

  .person { position: absolute; right: 295px; top: 170px; text-align: right; }
  .person .name { font-weight: 700; font-size: 16.5px; color: var(--brand-red); }
  .person .role { font-size: 11px; color: var(--ink); margin-top: 3px; }

  .divider {
    position: absolute; left: 235px; top: 143px; width: 2px; height: 104px;
    background: linear-gradient(to bottom, rgba(181,30,45,0), var(--brand-red) 35%, var(--brand-red) 65%, rgba(181,30,45,0));
  }

  .contacts { position: absolute; left: 262px; top: 167px; list-style: none; }
  .contacts li { display: flex; align-items: center; gap: 7px; font-size: 12px; color: var(--ink); height: 18px; margin-bottom: 7px; }
  .contacts svg { width: 18px; height: 18px; flex: none; }

  .address-band {
    position: absolute; left: 0; right: 0; bottom: 0; height: 30px;
    background: var(--brand-red); color: var(--white);
    font-weight: 700; font-size: 12px; display: flex; align-items: center; justify-content: center;
  }
</style>
</head>
<body>
  <section class="card card--back" aria-label="Card back">
    <div class="halo"></div>
    <p class="wordmark">Quorva</p>
    <p class="website">www.quorvawebsite.com</p>
  </section>

  <section class="card card--front" aria-label="Card front">
    <div class="brand">
      <span class="dot"></span>
      <span class="wordmark">Quorva</span>
    </div>

    <div class="person">
      <p class="name">Marcus Delano</p>
      <p class="role">Owner &amp; Founder</p>
    </div>

    <div class="divider"></div>

    <ul class="contacts">
      <li>
        <svg viewBox="0 0 18 18" aria-hidden="true">
          <circle cx="9" cy="9" r="9" fill="#b51e2d"/>
          <path d="M5 7.5c0-1.2 1.8-2 4-2s4 .8 4 2v.8h-2.2v-.9H7.2v.9H5z M6 9.2h6l.8 3.3H5.2z" fill="#fff"/>
        </svg>
        (555) 014-7396
      </li>
      <li>
        <svg viewBox="0 0 18 18" aria-hidden="true">
          <circle cx="9" cy="9" r="9" fill="#b51e2d"/>
          <rect x="4.5" y="6" width="9" height="6.4" fill="#fff"/>
          <path d="M4.5 6l4.5 3.6L13.5 6" fill="none" stroke="#b51e2d" stroke-width="0.9"/>
        </svg>
        MarcusD@quorvaweb.com
      </li>
    </ul>

    <div class="address-band">4172 Marlowe blvd, Ashfield Park, NV 89431</div>
  </section>
</body>
</html>
```